Web Design Project

Website Design Brief

Company Details
1a) Name of Company

MAPLEHAVEN
1) What is the nature of your business?: Briefly describe your products or services:

INDEPENDENT CONTEMPORARY TRADITIONAL ITALIAN RESTAURANT IN THE HEART OF ELMSWORTH QUAY ALSO CATERING FOR PRIVATE CORPORATE EVENTS AND WEDDING RECEPTIONS

1a) Who is your target market? Who are you hoping to reach with your site?

CITY CORPORATES, LOCAL CORPORATES/BUSINESSES, LOCAL RESIDENTS, VISITORS TO THE DOCK, LOCAL HOTELS

Website Details
1b) Do you have an existing website? If so, what is the URL?
HTTP://WWW.MAPLEHAVENTRATTORIA.EXAMPLE

2b) IMPORTANT: Please list at least 3 URLs (web addresses) of high quality sites that you like the look of (these do not have to be sites who’s business is similar to yours. It aids us in determining what your design style is.) Please consider layout, colours, navigation, graphics, and typography.

http://www.thecorvelle.example/

http://www.dunmorrow.example/

http://www.pavokitchen.example/

http://www.ilfaro.example/

3b) What colours or colour schemes would you like?

WHITE, BLACK, SILVER/ALUMINIUM (PLS LOOK AT OUR OUTSIDE CHAIRS)

4b) List the Navigation links for your Site:

5b) What type of look are you trying to achieve? (e.g. clean, high-tech, conservative, warm, flashy, etc.)

SIMPLE ELEGANT CLASSY INFORMATIVE, EASY TO USE, A REFLECTION OF THE BUSINESS ITSELF

6b) Please provide the addresses of competitors' sites, if possible:

Do not contact the client direct - all questions should go through Brightwell Venues - info@brightwellvenues.example
Updates

thanks for the designs that I have received so far. I have these general comments:

- please avoid using icons for phones or paperclips etc 
- use dummy text (one design used text from another website) 
- there won't any live social media feeds to the site
the client likes a lot of the designs that this company comes up with: 

i look forward to see some more designs

hi all, 

further to my last update, here are a few more pointers:
- there will be no search facilities - so no "search" box please 
- please just use the images supplied - no stock ones
- use just the page names give (no other pages) 

The client is looking for a simple, elegant design. 

Many thanks 
Rolf 

thanks for all the designs. 

I have uploaded another file to the brief which shows some posters that the client particularly likes. Perhaps the homepage could consist of large rectangle made up of a number of boxes - for some introductory text, a large image, mailing list, contact details, Lunch Special etc - just an idea! 
It's clear that the client likes clean lines with square edges. 
I want to be able to pass the designs directly onto the client so can designers avoid adding extra info or page. For example one design has a tab for a "Gift Card" - it will be easier for me if such additions are avoided. 

thanks!                                                                                                                                                                                                                                                                                                                                                                                                    

Thank you for all your designs - please keep them coming! 

hi all,

I am meeting the client tomorrow afternoon so please submit revisions / designs before then. 

Many thanks, 
Rolf

Target Market(s)

Business people, upmarket etc

Industry/Entity Type

Business

Requirements
Must have
• - The home page needs a slide show of images as well as:
- a mailing list form - very simple, "Join our mailing list - name, email"
- 3 or 4 sentences of text
- facebook link

```html
<!DOCTYPE html>
<html lang="en">
<head>
<meta charset="utf-8">
<title>Maplehaven Italian</title>
<link href="https://fonts.googleapis.com/css2?family=Arimo:wght@400;700&family=Libre+Baskerville&display=swap" rel="stylesheet">
<style>
:root{
  --bar:#353535;
  --bar-dark:#222;
  --page:#ececec;
  --ink:#333;
  --muted:#999;
  --accent:#b23a1b;
  --line:#c9c9c9;
  --white:#fff;
  --field:#5a5a5a;
}
*{box-sizing:border-box;margin:0;padding:0}
html,body{width:750px;height:1200px;overflow:hidden}
body{position:relative;background:var(--page);font-family:Arimo,Arial,sans-serif;color:var(--ink)}
.abs{position:absolute}

.main-nav{position:absolute;left:0;top:0;width:750px;height:37px;background:var(--bar)}
.main-nav a{position:absolute;top:12px;color:var(--white);font-size:11px;font-weight:700;letter-spacing:1.3px;text-decoration:none;transform:translateX(-50%)}
.main-nav a.current{top:7px;left:53px;width:75px;height:24px;line-height:22px;text-align:center;background:var(--bar-dark);border:1px solid #777;border-radius:4px}

.header-rule{position:absolute;top:97px;height:1px;background:#555}
.brand{position:absolute;left:0;width:750px;top:70px;text-align:center;font-size:26px;letter-spacing:3px;color:#111}
.brand small{display:block;font-size:10px;letter-spacing:3px;margin-top:2px}
.phone{position:absolute;right:28px;top:56px;font-family:"Libre Baskerville",serif;font-size:20px;letter-spacing:1px;color:#333}
.call{position:absolute;right:30px;top:82px;font-size:10px;letter-spacing:1px;color:var(--muted)}

.slider{position:absolute;left:16px;top:151px;width:716px;height:341px;background:radial-gradient(ellipse at 30% 30%,#777,#2a2a2a 75%)}
.slider .caption{position:absolute;left:0;bottom:0;width:100%;height:79px;background:rgba(0,0,0,.55)}
.slider .caption p{position:absolute;left:17px;top:25px;width:330px;color:var(--white);font-size:9.5px;line-height:12px}
.btn-dark{position:absolute;background:#2b2b2b;color:var(--white);font-size:9.5px;font-weight:700;text-align:center;border:1px solid #555}
.slider .btn-dark{left:585px;top:30px;width:111px;height:24px;line-height:22px;background:#444;border:none}
.dots{position:absolute;top:502px;left:332px;display:flex;gap:5px}
.dots span{width:11px;height:11px;border-radius:50%;background:#bbb}
.dots span:first-child{background:#111}

.restaurant-strip{position:absolute;left:16px;top:525px;width:716px;height:181px;background:#f7f7f7;border:1px solid var(--line)}
.restaurant-strip .divider{position:absolute;top:0;bottom:0;width:1px;background:var(--line)}
.section-red{position:absolute;color:var(--accent);font-size:11px;letter-spacing:1.3px}
.thumb{position:absolute;border:3px solid #e2e2e2;width:138px;height:106px}
.strip-text{position:absolute;width:145px;font-size:7.5px;line-height:9.5px;color:#222}

h2{position:absolute;font-size:14px;font-weight:700;letter-spacing:1.5px;color:#2a2a2a}
.photo-frame{position:absolute;width:231px;height:165px;background:var(--white)}
.photo-frame div{position:absolute;left:7px;top:10px;width:217px;height:144px}
.lead{position:absolute;width:215px;font-size:9.8px;line-height:13.6px;color:var(--accent);letter-spacing:.3px}
.body{position:absolute;width:200px;font-size:8.6px;line-height:13.5px;color:#333;letter-spacing:.3px}
.read-more{width:68px;height:28px;line-height:26px;font-weight:400;font-size:9.5px;letter-spacing:.5px}

.booking{position:absolute;left:261px;top:759px;width:224px;height:331px;background:#eee;border:2px solid #aaa}
.booking .title{position:absolute;left:0;width:100%;top:7px;text-align:center;font-family:"Libre Baskerville",serif;font-size:8px;color:#222}
.booking .sub{position:absolute;left:0;width:100%;top:17px;text-align:center;font-size:6px;color:#444}
.booking .flag{position:absolute;left:203px;top:5px;width:12px;height:9px;background:#d9d9e6;border:1px solid #aaa}
.booking .hero{position:absolute;left:7px;top:35px;width:206px;height:110px;background:linear-gradient(135deg,#e7b24c,#9a3a16 60%,#3a1d10)}
.booking .label{position:absolute;left:6px;top:162px;font-size:7px;color:#444}
.select{position:absolute;top:172px;height:15px;background:var(--white);border:1px solid #bbb;font-size:8px;line-height:13px;padding-left:3px}
.cal-head{position:absolute;left:5px;top:191px;width:209px;height:12px;background:linear-gradient(#ddd,#bbb);border:1px solid #aaa;text-align:center;font-size:7.5px;line-height:11px}
.cal-head span{position:absolute;right:4px;top:0;font-size:8px}
.calendar{position:absolute;left:5px;top:203px;width:209px;border-collapse:collapse;font-size:8px;text-align:center}
.calendar th{height:11px;background:#ccc;font-size:7px;font-weight:400;border:1px solid #aaa}
.calendar td{height:14px;background:var(--white);border:1px solid #bbb}
.calendar td.off{background:#ddd;color:#999}
.calendar td.sel{outline:2px solid #d44;outline-offset:-2px}
.calendar td.full{color:#d44;text-decoration:line-through}
.booking .foot{position:absolute;left:0;bottom:0;width:100%;height:22px;background:linear-gradient(#ddd,#bbb);border-top:1px solid #aaa}
.booking .foot b{position:absolute;right:8px;top:6px;font-size:7px;font-weight:700;color:#444}

.site-footer{position:absolute;left:0;top:1110px;width:750px;height:90px;background:var(--bar)}
.site-footer ul{position:absolute;top:13px;list-style:none}
.site-footer li{font-size:9.5px;letter-spacing:1.2px;color:var(--white);line-height:13.5px}
.newsletter{position:absolute;left:570px;top:8px;font-size:9.5px;font-weight:700;letter-spacing:1px;color:var(--white)}
.field-label{position:absolute;left:570px;font-size:8px;color:#ccc}
.field{position:absolute;left:601px;width:140px;height:18px;background:var(--field)}
.submit{left:672px;top:70px;width:69px;height:18px;line-height:17px;background:#111;border:none;letter-spacing:1.5px;font-weight:400}
.share{position:absolute;left:334px;top:62px;width:100px;height:28px;background:#555;border-radius:4px 4px 0 0;display:flex;gap:3px;padding:5px 7px}
.share span{width:20px;height:20px;background:#8aa;border-radius:2px}
</style>
</head>
<body>

<nav class="main-nav">
  <a class="current" href="#">WELCOME</a>
  <a href="#" style="left:174px">OUR RESTAURANT</a>
  <a href="#" style="left:290px">OUR MENU</a>
  <a href="#" style="left:391px">GALLERY</a>
  <a href="#" style="left:482px">EVENTS</a>
  <a href="#" style="left:586px">RESERVATION</a>
  <a href="#" style="left:694px">CONTACT</a>
</nav>

<header>
  <div class="header-rule" style="left:18px;width:218px"></div>
  <div class="header-rule" style="left:510px;width:215px"></div>
  <div class="brand">MAPLEHAVEN<small>ITALIAN</small></div>
  <div class="phone">-1800 555 0172</div>
  <div class="call">Call for info</div>
</header>

<section class="slider" role="img" aria-label="Slideshow photo of wine glasses and dishes on a restaurant table">
  <div class="caption">
    <p>Lorem ipsum dolor sit amet, consectetuer adipiscing elit, sed diam nonummy nibh euismod tincidunt ut laoreet dolore magna aliquam erat volutpat.</p>
    <div class="btn-dark">RESERVATION NOW !</div>
  </div>
</section>
<div class="dots"><span></span><span></span><span></span><span></span><span></span></div>

<section class="restaurant-strip">
  <div class="divider" style="left:216px"></div>
  <div class="divider" style="left:499px"></div>
  <div class="section-red" style="left:9px;top:10px">OUR RESTAURANT</div>
  <svg class="abs" style="left:691px;top:7px" width="16" height="10" viewBox="0 0 16 10"><path d="M6 1 2 5l4 4M10 1l4 4-4 4" fill="none" stroke="#999" stroke-width="1.5"/></svg>

  <div class="thumb" role="img" aria-label="Salad dish" style="left:21px;top:31px;background:linear-gradient(135deg,#5f9a3c,#e8e2d4 55%,#b5402a)"></div>
  <p class="strip-text" style="left:24px;top:141px">Lorem ipsum dolor sit amet, con-sectetuer adipiscing elit, sed diam nonummy nibh euismod tincidunt ut laoreet dolore magna</p>

  <div class="thumb" role="img" aria-label="Diner holding knife and fork at a checked table" style="left:285px;top:31px;background:linear-gradient(#c3302a,#e6cfc0 60%,#c33)"></div>
  <p class="strip-text" style="left:288px;top:141px">Lorem ipsum dolor sit amet, con-sectetuer adipiscing elit, sed diam nonummy nibh euismod tincidunt ut laoreet dolore magna</p>

  <div class="thumb" role="img" aria-label="Champagne glasses" style="left:563px;top:31px;background:linear-gradient(135deg,#1d4c7a,#d9b25a 55%,#12314f)"></div>
  <p class="strip-text" style="left:566px;top:141px">Lorem ipsum dolor sit amet, con-sectetuer adipiscing elit, sed diam nonummy nibh euismod tincidunt ut laoreet dolore magna</p>
</section>

<section>
  <h2 style="left:19px;top:731px">WELCOME!</h2>
  <div class="photo-frame" style="left:19px;top:758px"><div role="img" aria-label="Restaurant building lit at night" style="background:linear-gradient(#1a1a22,#4a3a2a 70%,#2a2218)"></div></div>
  <p class="lead" style="left:22px;top:930px">Lorem ipsum dolor sit amet, consectetuer adipiscing elit, sed diam nonummy nibh euismod tincidunt ut laoreet dolore magna aliquam erat volutpat.</p>
  <p class="body" style="left:24px;top:996px">Lorem ipsum dolor sit amet, consectetuer adipiscing elit, sed diam nonummy nibh euismod tincidunt ut laoreet dolore magna aliquam erat volutpat.</p>
  <div class="btn-dark read-more" style="left:183px;top:1055px">Read more</div>
</section>

<section>
  <h2 style="left:259px;top:731px">RESERVATIONS</h2>
  <div class="booking">
    <div class="title">The Maplehaven Italian</div>
    <div class="sub">STANDARD À LA CARTE MENU</div>
    <div class="flag"></div>
    <div class="hero" role="img" aria-label="Reserved sign on a restaurant table"></div>
    <div class="label">Select your preferred party size (max 60) and session</div>
    <div class="select" style="left:5px;width:38px">2</div>
    <div class="select" style="left:45px;width:169px">Dinner</div>
    <div class="cal-head">MARCH 2012<span>▶</span></div>
    <table class="calendar">
      <tr><th>MON</th><th>TUE</th><th>WED</th><th>THU</th><th>FRI</th><th>SAT</th><th>SUN</th></tr>
      <tr><td class="off">27</td><td class="off">28</td><td class="off">29</td><td class="off">1</td><td class="off">2</td><td class="off">3</td><td class="off">4</td></tr>
      <tr><td class="off">5</td><td class="off">6</td><td class="off">7</td><td class="off">8</td><td class="sel">9</td><td>10</td><td>11</td></tr>
      <tr><td>12</td><td>13</td><td>14</td><td>15</td><td>16</td><td>17</td><td>18</td></tr>
      <tr><td>19</td><td>20</td><td>21</td><td>22</td><td>23</td><td>24</td><td>25</td></tr>
      <tr><td>26</td><td>27</td><td>28</td><td>29</td><td class="full">30</td><td>31</td><td class="off">1</td></tr>
      <tr><td class="off">2</td><td class="off">3</td><td class="off">4</td><td class="off">5</td><td class="off">6</td><td class="off">7</td><td class="off">8</td></tr>
    </table>
    <div class="foot">
      <svg class="abs" style="left:102px;top:3px" width="14" height="14" viewBox="0 0 14 14"><circle cx="7" cy="7" r="6.5" fill="#fff" stroke="#999"/><path d="M7 11 3.5 7.2a2 2 0 0 1 3.5-2 2 2 0 0 1 3.5 2z" fill="#c33"/></svg>
      <b>BOOK A TABLE ▶</b>
    </div>
  </div>
</section>

<section>
  <h2 style="left:500px;top:731px">OUR SERVICES</h2>
  <div class="photo-frame" style="left:500px;top:758px"><div role="img" aria-label="Outdoor terrace tables by the quay" style="background:linear-gradient(#7a6a58,#a8a49a 55%,#cfd3dc)"></div></div>
  <p class="lead" style="left:503px;top:930px">Lorem ipsum dolor sit amet, consectetuer adipiscing elit, sed diam nonummy nibh euismod tincidunt ut laoreet dolore magna aliquam erat volutpat.</p>
  <p class="body" style="left:505px;top:996px">Lorem ipsum dolor sit amet, consectetuer adipiscing elit, sed diam nonummy nibh euismod tincidunt ut laoreet dolore magna aliquam erat volutpat.</p>
  <div class="btn-dark read-more" style="left:664px;top:1055px">Read more</div>
</section>

<footer class="site-footer">
  <ul style="left:16px"><li>WELCOME</li><li>OUR RESTAURANT</li><li>OUR MENU</li><li>GALLERY</li><li>EVENTS</li></ul>
  <ul style="left:174px"><li>RESERVATION</li><li>CONTACT</li></ul>
  <div class="newsletter">NEWSLETTER SIGNUP</div>
  <div class="field-label" style="top:33px">Name</div>
  <div class="field" style="top:27px"></div>
  <div class="field-label" style="top:52px">Email</div>
  <div class="field" style="top:47px"></div>
  <div class="btn-dark submit">SUBMIT</div>
  <div class="share"><span></span><span></span><span></span><span></span></div>
</footer>

</body>
</html>
```